2018 Vision Board Workshop

I need to promote this workshop on both an 8.5x11 sheet and a 5x7 card. I do have a logo that needs to be present. I'd like to stay true to my branded colors. The flyer needs to project the excitement of a new year and the possibilities of what a person can create, produce, explore in their lives by putting it all on a vision board. Creating the vision of what you want will inspire you to achieve your goals and dreams. Looking at your vision board each day will propel you into taking action as you chart your course to achieve what you truly want.
The flyer needs to have the following information:
The workshop date and time - Sat., Jan. 13, 2018, 10:30-1:30
The location is - Studio 47B, 2486 Maple Ridge Ln, Colorado Springs, Co 80920
in the BUILD Room
My name and contact information - Mara Lindqvist
Text and voice 303-614-7752
Email - mara@bright-path-forward.com
Website - bright-path-forward.com
The fee is $45. All materials are provided.

My company is called Bright Path Forward. I am a Life Coach, author, speaker and workshop leader.\ I wrote this program, Bright Path Forward to teach concepts and supporting skills for living with more happiness, satisfaction and fulfillment. Thanks for reading this!! Mara

Target Market(s)

Primarily women, educated, motivated, proactive in their own lives and well being

Font styles to use
Other font styles liked:
• I have been using Century Gothic. I'm open to new ideas.

Requirements
Must have
• The Bright Path Forward logo
• The flyer needs to have the following information:
• The workshop date and time - Sat., Jan. 13, 2018, 10:30-1:30
• The location is - Studio 47B, 2486 Maple Ridge Ln, Colorado Springs, Co 80920
• in the BUILD Room
• My name and contact information - Mara Lindqvist
• Text and voice 303-614-7752
• Email - mara@bright-path-forward.com
• Website - bright-path-forward.com
• The fee is $45. All materials are provided.
Nice to have
• The Bright Path Forward branded colors in the design
• Images of vision boards

```html
<!DOCTYPE html>
<html lang="en">
<head>
<meta charset="utf-8">
<title>2018 Vision Board Workshop – Bright Path Forward</title>
<link rel="stylesheet" href="https://fonts.googleapis.com/css2?family=Open+Sans:wght@400;600;700&family=Questrial&display=swap">
<style>
  :root {
    --white: #ffffff;
    --brand-green: #8cc63f;
    --brand-blue: #4aa9de;
    --band-blue: #4badE0;
    --heading-navy: #1f5894;
    --frame-blue: #5a7fc0;
    --body-ink: #222222;
    --hero-mint: #cfe8c9;
    --hero-cream: #f4f1d8;
  }
  * { box-sizing: border-box; margin: 0; padding: 0; }
  html, body { width: 932px; height: 1200px; overflow: hidden; background: var(--white); }
  .flyer { position: relative; width: 932px; height: 1200px; overflow: hidden; background: var(--white); font-family: "Questrial", "Century Gothic", sans-serif; color: var(--body-ink); }

  .hero-photo {
    position: absolute; left: 0; top: 0; width: 932px; height: 600px;
    background:
      radial-gradient(ellipse 220px 180px at 330px 150px, rgba(233,137,106,.85), rgba(241,194,122,.45) 60%, transparent 100%),
      radial-gradient(ellipse 420px 300px at 560px 260px, rgba(244,241,216,.9), transparent 75%),
      radial-gradient(ellipse 380px 420px at 120px 280px, rgba(169,214,160,.95), transparent 80%),
      radial-gradient(ellipse 360px 300px at 820px 140px, rgba(207,232,201,.9), transparent 80%),
      linear-gradient(180deg, var(--hero-mint) 0%, var(--hero-cream) 55%, var(--white) 100%);
  }
  .hero-fade { position: absolute; left: 0; top: 470px; width: 932px; height: 130px; background: linear-gradient(180deg, rgba(255,255,255,0) 0%, var(--white) 85%); }

  .headline {
    position: absolute; left: 0; top: 282px; width: 932px; text-align: center;
    font-family: "Open Sans", sans-serif; font-weight: 600; font-size: 65px; line-height: 80px;
    letter-spacing: 1px; color: var(--white); text-transform: uppercase;
  }

  .fee-badge { position: absolute; left: 746px; top: 488px; width: 152px; height: 152px; }
  .fee-badge-text {
    position: absolute; left: 746px; top: 519px; width: 152px; text-align: center;
    font-family: "Open Sans", sans-serif; font-size: 16px; line-height: 23px; color: var(--white);
  }

  .brand-name {
    position: absolute; left: 0; top: 652px; width: 932px; text-align: center;
    font-family: "Questrial", sans-serif; font-size: 44px; line-height: 54px; color: var(--brand-green);
  }
  .brand-dot { display: inline-block; width: 18px; height: 18px; border-radius: 50%; background: var(--brand-blue); margin-right: 14px; vertical-align: 4px; }

  .intro {
    position: absolute; left: 16px; top: 750px; width: 900px; text-align: center;
    font-size: 20px; line-height: 26px; letter-spacing: 0.4px; color: var(--body-ink);
  }

  .event-title {
    position: absolute; left: 0; top: 842px; width: 932px; text-align: center;
    font-family: "Open Sans", sans-serif; font-weight: 700; font-size: 31px; color: var(--heading-navy);
  }
  .event-when {
    position: absolute; left: 66px; top: 895px; width: 810px; height: 66px;
    border: 1.5px solid var(--frame-blue); display: flex; align-items: center; justify-content: center;
    font-size: 30px; color: var(--body-ink);
  }
  .event-where {
    position: absolute; left: 250px; top: 988px; width: 460px; text-align: center;
    font-size: 17.5px; line-height: 23px; color: var(--body-ink);
  }

  .contact-band { position: absolute; left: 0; top: 1064px; width: 932px; height: 136px; background: var(--band-blue); }
  .host-name {
    position: absolute; left: 0; top: 1080px; width: 932px; text-align: center;
    font-family: "Questrial", sans-serif; font-size: 36px; color: var(--white);
  }
  .contact-list { position: absolute; top: 1138px; left: 0; width: 932px; height: 26px; list-style: none; }
  .contact-item {
    position: absolute; display: flex; align-items: center; gap: 9px;
    font-family: "Open Sans", sans-serif; font-weight: 600; font-size: 18px; color: var(--white);
  }
  .contact-item svg { width: 18px; height: 18px; }
  .contact-email { left: 76px; }
  .contact-phone { left: 403px; }
  .contact-web { left: 603px; }

  .host-portrait {
    position: absolute; left: 46px; top: 966px; width: 162px; height: 162px; border-radius: 50%;
    border: 5px solid var(--white); box-shadow: 0 0 0 1px #d9d9d9;
    background: radial-gradient(circle at 50% 40%, #f0d3b4 0%, #e4b98f 35%, #c98d3c 70%, #7f7a3a 100%);
  }
</style>
</head>
<body>
<main class="flyer">
  <div class="hero-photo" role="img" aria-label="Joyful woman with arms spread wide in a soft wintry light with snowflakes"></div>
  <div class="hero-fade"></div>

  <h1 class="headline">What you think is<br>what you create</h1>

  <svg class="fee-badge" viewBox="0 0 150 150" aria-hidden="true">
    <g fill="var(--brand-blue)" transform="translate(75 75)">
      <rect x="-58" y="-58" width="116" height="116"/>
      <rect x="-58" y="-58" width="116" height="116" transform="rotate(15)"/>
      <rect x="-58" y="-58" width="116" height="116" transform="rotate(30)"/>
      <rect x="-58" y="-58" width="116" height="116" transform="rotate(45)"/>
      <rect x="-58" y="-58" width="116" height="116" transform="rotate(60)"/>
      <rect x="-58" y="-58" width="116" height="116" transform="rotate(75)"/>
    </g>
  </svg>
  <p class="fee-badge-text">The fee is $45.<br>All materials<br>are provided.</p>

  <div class="brand-name"><span class="brand-dot"></span>Bright Path Forward</div>

  <p class="intro">Creating the vision of what you want will inspire you to achieve your goals and<br>dreams. Looking at your vision board each day will propel you into taking action<br>as you chart your course to achieve what you truly want.</p>

  <h2 class="event-title">2018 VISION BOARD WORKSHOP</h2>
  <p class="event-when">Sat., Jan. 13, 2018, 10:30-1:30</p>
  <p class="event-where">Studio 47B, BUILD Room, 2486 Maple Ridge<br>Ln, Colorado Springs, Co 80920</p>

  <section class="contact-band"></section>
  <div class="host-portrait" role="img" aria-label="Portrait photo of the workshop host, Mara Lindqvist"></div>
  <p class="host-name">Mara Lindqvist</p>
  <ul class="contact-list">
    <li class="contact-item contact-email">
      <svg viewBox="0 0 18 18" aria-hidden="true"><circle cx="9" cy="9" r="9" fill="var(--white)"/><rect x="4" y="5.5" width="10" height="7" rx="1" fill="var(--band-blue)"/><path d="M4.5 6.2 9 9.6l4.5-3.4" stroke="var(--white)" stroke-width="1" fill="none"/></svg>
      mara@bright-path-forward.com
    </li>
    <li class="contact-item contact-phone">
      <svg viewBox="0 0 18 18" aria-hidden="true"><circle cx="9" cy="9" r="8" fill="none" stroke="var(--white)" stroke-width="1.6"/><path d="M6 5.2c.6-.4 1.1-.3 1.4.2l.6 1.2c.2.4.1.8-.3 1.1l-.4.3c.4 1 1.2 1.8 2.2 2.2l.3-.4c.3-.4.7-.5 1.1-.3l1.2.6c.5.3.6.8.2 1.4-.6.8-1.6 1-2.6.5-2-1-3.3-2.3-4.3-4.3-.5-1-.3-2 .6-2.5z" fill="var(--white)"/></svg>
      303-614-7752
    </li>
    <li class="contact-item contact-web">
      <svg viewBox="0 0 18 18" aria-hidden="true"><circle cx="9" cy="9" r="8" fill="none" stroke="var(--white)" stroke-width="1.6"/><g fill="none" stroke="var(--white)" stroke-width="1"><circle cx="9" cy="9" r="4.6"/><ellipse cx="9" cy="9" rx="2" ry="4.6"/><path d="M4.4 9h9.2"/></g></svg>
      www.bright-path-forward.com
    </li>
  </ul>
</main>
</body>
</html>
```